Packaging design for a reclosable bag for our product

We have a logo, and we need to put it on packaging for our product and while we want the look to be simple, we want it to follow good design principles and also contain spaces for other product descriptions.

There will be 5 sizes at launch so I'd like 5 variations, one for each size.

I've included a few mockups of the type of bag that I made but they are all just rough ideas that I had.

I want the brand to look scientific and methodical and even a bit quirky, as in "wow this is a serious product but also a bit unusual."

```html
<!DOCTYPE html>
<html lang="en">
<head>
<meta charset="utf-8">
<title>QV7 Bias Lighting – Pouch Packaging</title>
<link rel="stylesheet" href="https://fonts.googleapis.com/css2?family=Comfortaa:wght@400;500;700&display=swap">
<style>
  :root {
    --backdrop: #cfcfcf;
    --pouch-black: #0c0c0c;
    --pouch-silver: #dcdcdc;
    --ink-silver: #e8e8e8;
    --ink-black: #0c0c0c;
    --seam: #1e1e1e;
  }
  * { margin: 0; padding: 0; box-sizing: border-box; }
  html, body {
    width: 1200px; height: 783px; overflow: hidden;
    background: var(--backdrop);
    font-family: "Comfortaa", sans-serif;
  }
  .canvas { position: relative; width: 1200px; height: 783px; }

  .pouch {
    position: absolute; top: 91px; width: 404px; height: 584px;
    border-radius: 4px 4px 6px 6px; overflow: hidden;
    background: var(--pouch-black);
  }
  .pouch--split { left: 149px; }
  .pouch--dark { left: 650px; }

  .pouch__zip {
    position: absolute; left: 14px; right: 14px; top: 68px;
    height: 2px; background: var(--seam);
  }
  .pouch__lower {
    position: absolute; left: 0; right: 0; top: 330px; bottom: 0;
    background: var(--pouch-silver);
  }

  .brand-name {
    position: absolute; left: 0; right: 0; top: 112px;
    text-align: center; color: var(--ink-silver);
    font-weight: 700; font-size: 168px; line-height: 1;
    letter-spacing: -6px;
  }
  .brand-line {
    position: absolute; left: 0; right: 0; top: 283px;
    text-align: center; color: var(--ink-silver);
    font-weight: 500; font-size: 31px; line-height: 1;
    letter-spacing: 1px;
  }

  .size-tag {
    position: absolute; font-weight: 700; font-size: 16px; line-height: 1;
    letter-spacing: 0.5px; white-space: nowrap;
  }
  .pouch--split .size-tag {
    left: 186px; top: 360px; padding: 3px 10px 3px 10px;
    background: var(--ink-black); color: var(--pouch-silver);
    border-radius: 12px;
  }
  .pouch--dark .size-tag {
    left: 197px; top: 350px; color: var(--ink-silver); font-weight: 500;
  }

  .size-value {
    position: absolute; left: 0; right: 0;
    text-align: center; line-height: 1; letter-spacing: -4px;
  }
  .pouch--split .size-value {
    top: 334px; font-size: 176px; font-weight: 700; color: var(--ink-black);
    padding-right: 8px;
  }
  .pouch--dark .size-value {
    top: 326px; font-size: 170px; font-weight: 400; color: var(--ink-silver);
    padding-left: 14px;
  }

  .spec {
    position: absolute; left: 0; right: 0;
    text-align: center; font-weight: 500; font-size: 15px; line-height: 20px;
  }
  .pouch--split .spec { top: 496px; color: var(--ink-black); }
  .pouch--dark .spec { top: 486px; color: var(--ink-silver); }
</style>
</head>
<body>
<main class="canvas">

  <section class="pouch pouch--split" aria-label="Extra large 5 metre pouch, split colourway">
    <div class="pouch__zip"></div>
    <div class="pouch__lower"></div>
    <div class="brand-name">QV7</div>
    <div class="brand-line">BIAS LIGHTING</div>
    <div class="size-value">5m</div>
    <div class="size-tag">EXTRA LARGE</div>
    <p class="spec">6500K White Bias Lighting<br>Simulated D65 CRI 90+</p>
  </section>

  <section class="pouch pouch--dark" aria-label="Extra large 5 metre pouch, dark colourway">
    <div class="pouch__zip"></div>
    <div class="brand-name">QV7</div>
    <div class="brand-line">BIAS LIGHTING</div>
    <div class="size-value">5m</div>
    <div class="size-tag">EXTRA LARGE</div>
    <p class="spec">6500K White Bias Lighting<br>Simulated D65 CRI 90+</p>
  </section>

</main>
</body>
</html>
```